Young, dynamic furniture company needs a new business card design

We require a new business card design for our modern furniture company which supplies furniture and appliances to the property and development market.
Oakridge Interiors has become one of the leading furniture & appliance suppliers to the property market withing London. With over 10 years experience, we have increased our business to supply not only private landlords and managing agents, but also property developers, housing associations and local councils.
We offer not only a complete range of furniture which includes beds, wardrobes, dining sets and sofas, but also a high quality, full delivery and assembly service to help you with all our furnishing needs.

Target Market(s)

Private landlords, estate agents, letting agents, property management companies

Industry/Entity Type

Business

Contact Information for Business Card

Name,
Title,
Address,
Mobile,
Telephone,
Fax, Website, email address

Font styles to use
Sans Serif

Colors
3176b5
0555a3
85abd2
cfdeed

Requirements
Must have
• All the above information for each of our staff, along with our logo

```html
<!DOCTYPE html>
<html lang="en">
<head>
<meta charset="utf-8">
<title>Oakridge Interiors – Business Card</title>
<link href="https://fonts.googleapis.com/css2?family=Roboto+Condensed:wght@300;400&family=Roboto:wght@300;400;500&display=swap" rel="stylesheet">
<style>
  :root {
    --page-bg: #e9e7e3;
    --card-top: #ffffff;
    --card-bottom: #e7e8ea;
    --ink: #2b2b2d;
    --ink-soft: #4a4b4e;
    --blue-line: #3176b5;
    --blue-deep: #0555a3;
    --blue-icon: #1b8fd0;
    --blue-mark: #2d4a9a;
  }
  * { box-sizing: border-box; margin: 0; padding: 0; }
  html, body { width: 1200px; height: 1023px; overflow: hidden; }
  body {
    background: var(--page-bg);
    display: flex;
    flex-direction: column;
    align-items: center;
    justify-content: center;
    gap: 60px;
    font-family: "Roboto", sans-serif;
    color: var(--ink);
  }
  .card {
    position: relative;
    width: 700px;
    height: 400px;
    border-radius: 18px;
    background: linear-gradient(160deg, var(--card-top) 0%, #f6f6f7 45%, var(--card-bottom) 100%);
    box-shadow: 0 2px 0 #d2d3d6, 0 4px 0 #c7c8cb, 0 10px 24px rgba(0,0,0,.18);
    overflow: hidden;
  }

  /* Front */
  .divider {
    position: absolute;
    left: 0; right: 150px;
    top: 206px;
    height: 1px;
    background: var(--blue-line);
  }
  .brand {
    position: absolute;
    left: 48px;
    top: 118px;
    display: flex;
    align-items: center;
    gap: 14px;
  }
  .brand-square {
    width: 60px; height: 60px;
    background: var(--blue-mark);
  }
  .brand-name {
    font-family: "Roboto Condensed", sans-serif;
    font-weight: 300;
    font-size: 29px;
    letter-spacing: .5px;
    text-transform: uppercase;
    color: var(--ink);
    line-height: 1;
  }
  .brand-tagline {
    font-family: "Roboto Condensed", sans-serif;
    font-weight: 300;
    font-size: 13px;
    text-transform: uppercase;
    color: var(--ink-soft);
    margin-top: 4px;
  }
  .phones {
    position: absolute;
    left: 48px;
    top: 240px;
    list-style: none;
    font-size: 16px;
    font-weight: 300;
    letter-spacing: 1px;
    color: var(--ink-soft);
  }
  .phones li, .contacts li {
    display: flex;
    align-items: center;
    gap: 14px;
    height: 34px;
  }
  .icon { width: 14px; height: 14px; fill: var(--blue-icon); flex: none; }
  .person {
    position: absolute;
    right: 40px;
    top: 128px;
    text-align: right;
  }
  .person-name {
    font-size: 36px;
    font-weight: 400;
    letter-spacing: 1.5px;
    color: var(--ink);
    line-height: 1;
  }
  .person-rule {
    height: 1px;
    background: var(--blue-line);
    margin: 6px 0 4px 0;
  }
  .person-title {
    font-size: 15px;
    font-weight: 500;
    letter-spacing: 1px;
    color: var(--ink);
  }
  .contacts {
    position: absolute;
    right: 40px;
    top: 226px;
    list-style: none;
    font-size: 15px;
    font-weight: 300;
    letter-spacing: 1px;
    color: var(--ink-soft);
  }
  .contacts li { justify-content: flex-end; }
  .contacts .icon { order: 2; }

  /* Back */
  .back-line {
    position: absolute;
    height: 1px;
    width: 300px;
    background: var(--blue-deep);
  }
  .back-line.top { left: 70px; top: 56px; }
  .back-line.bottom { right: 40px; bottom: 56px; }
  .back-brand {
    position: absolute;
    inset: 0;
    display: flex;
    flex-direction: column;
    align-items: center;
    justify-content: center;
    gap: 14px;
  }
  .back-brand .brand-square { width: 90px; height: 90px; }
  .back-brand .brand-name { font-size: 38px; }
  .back-brand .brand-tagline { font-size: 17px; text-align: center; margin-top: 0; }
</style>
</head>
<body>

<section class="card card-front" aria-label="Business card front">
  <div class="brand">
    <div class="brand-square"></div>
    <div>
      <div class="brand-name">Oakridge Interiors</div>
      <div class="brand-tagline">Trade Furniture Solutions</div>
    </div>
  </div>
  <div class="divider"></div>

  <ul class="phones">
    <li><svg class="icon" viewBox="0 0 16 16"><path d="M3.5 1l2.5 3-1.5 1.8c.8 1.9 2.2 3.3 4.2 4.2L10.5 8.5l3 2.5-1.2 2.8C7 13.5 2.5 9 2.2 3.7z"/></svg>88-123-54320</li>
    <li><svg class="icon" viewBox="0 0 16 16"><path d="M4 1h8v14H4zM5.5 2.5v9h5v-9zM7.2 12.5h1.6v1.2H7.2z"/></svg>88-123-54321</li>
    <li><svg class="icon" viewBox="0 0 16 16"><path d="M4 1h7v4H4zM2 6h12v7h-2v2H4v-2H2zM5 10v3.5h6V10zM11.5 7.5h1.3v1.3h-1.3z"/></svg>88-123-54322</li>
  </ul>

  <div class="person">
    <div class="person-name">Your Name</div>
    <div class="person-rule"></div>
    <div class="person-title">Title</div>
  </div>

  <ul class="contacts">
    <li><svg class="icon" viewBox="0 0 16 16"><path d="M1 3h14v10H1zM2.5 4.5L8 9l5.5-4.5v-.1h-11z"/></svg>info@yourweb.com</li>
    <li><svg class="icon" viewBox="0 0 16 16"><path d="M8 1a7 7 0 100 14A7 7 0 008 1zm0 1.3c.9 0 1.8 1.3 2.2 3.2H5.8C6.2 3.6 7.1 2.3 8 2.3zM2.5 6.8h2.9a10 10 0 000 2.4H2.5a5.7 5.7 0 010-2.4zm4.2 0h2.6a9 9 0 010 2.4H6.7a9 9 0 010-2.4zm3.9 0h2.9a5.7 5.7 0 010 2.4h-2.9a10 10 0 000-2.4zM5.8 10.5h4.4c-.4 1.9-1.3 3.2-2.2 3.2s-1.8-1.3-2.2-3.2z"/></svg>www.yourweb.com</li>
    <li><svg class="icon" viewBox="0 0 16 16"><path d="M8 1a5 5 0 00-5 5c0 3.5 5 9 5 9s5-5.5 5-9a5 5 0 00-5-5zm0 3a2 2 0 110 4 2 2 0 010-4z"/></svg>Your Address line1</li>
  </ul>
</section>

<section class="card card-back" aria-label="Business card back">
  <div class="back-line top"></div>
  <div class="back-brand">
    <div class="brand-square"></div>
    <div class="brand-name">Oakridge Interiors</div>
    <div class="brand-tagline">Trade Furniture Solutions</div>
  </div>
  <div class="back-line bottom"></div>
</section>

</body>
</html>
```